Computer consultant business card

Bexil Software is a newly started computer consulting company. It's a small one-man company that provides mostly Vornix applications but also websites in collaboration with designers. I'm running this company on the side of full time university studies.

I want the final design to be clean and memorable. Be creative! :)

Some inspiration:
http://www.pixelmarta.com/design/48317
http://www.pixelmarta.com/design/2739164/business-card-design-by-frostlynk
http://www.pixelmarta.com/design/604281/business-card-design-by-koralind-vestrabanu

See attachment for my company logo.
Updates

I would like to thank everyone for submitting! I'll need a couple of days to review and ultimately select a design.

Target Market(s)

Non-technical entrepreneurs and small companies.

Industry/Entity Type

University

Requirements
Must have
• My company logo.
In any way, both colors from my logo.
First- and last name, e-mail and phone number.
Double-sided design.
Nice to have
• Something creative with the symbol in my logo

```html
<!DOCTYPE html>
<html lang="en">
<head>
<meta charset="utf-8">
<title>Ovrik — Business Card</title>
<link rel="stylesheet" href="https://fonts.googleapis.com/css2?family=Tinos:wght@400;700&display=swap">
<style>
  :root {
    --stage: #8a8a8a;
    --card-dark: #050505;
    --card-light: #fbfbfb;
    --brand-blue: #3c64b4;
    --ink-dark: #232323;
    --ink-light: #f2f2f2;
    --ink-muted: #b8b8b8;
    --rule: #cfcfcf;
  }
  * { box-sizing: border-box; margin: 0; padding: 0; }
  html, body { width: 1200px; height: 787px; overflow: hidden; }
  body {
    background: var(--stage);
    font-family: "Tinos", "Times New Roman", serif;
    display: flex;
    align-items: center;
    justify-content: center;
    gap: 40px;
  }
  .card {
    position: relative;
    width: 540px;
    height: 320px;
    border-radius: 18px;
    box-shadow: 0 8px 24px rgba(0,0,0,0.35);
  }
  .card--front { background: var(--card-light); }
  .card--back { background: var(--card-dark); color: var(--ink-light); }

  .brand { display: flex; align-items: center; gap: 14px; }
  .brand__mark {
    width: 40px; height: 40px; border-radius: 50%;
    background: var(--brand-blue);
    flex: none;
  }
  .brand__name { font-size: 46px; font-weight: 400; line-height: 1; letter-spacing: 1px; }

  /* front */
  .front__lockup {
    position: absolute; left: 50%; top: 50%;
    transform: translate(-50%, -50%);
    display: flex; flex-direction: column; align-items: flex-start;
  }
  .front__lockup .brand__name { color: var(--ink-dark); }
  .front__position { margin-top: 6px; margin-left: 56px; font-size: 14px; color: var(--ink-dark); white-space: nowrap; }

  /* back */
  .back__brand { position: absolute; left: 40px; top: 56px; }
  .back__brand .brand__name { color: var(--ink-light); }
  .back__identity { position: absolute; right: 40px; top: 34px; text-align: center; width: 190px; }
  .back__name { font-size: 24px; color: var(--ink-muted); }
  .back__position { font-size: 12px; color: var(--ink-muted); }
  .back__lines { position: absolute; right: 36px; top: 112px; width: 250px; }
  .back__lines span { display: block; height: 1px; background: var(--rule); margin-bottom: 24px; }
  .contact { position: absolute; display: flex; align-items: center; gap: 10px; font-size: 15px; color: var(--ink-light); white-space: nowrap; }
  .contact__icon { width: 22px; height: 22px; flex: none; }
  .contact--phone { right: 44px; bottom: 62px; }
  .contact--email { left: 40px; bottom: 24px; }
</style>
</head>
<body>
  <section class="card card--front">
    <div class="front__lockup">
      <div class="brand">
        <span class="brand__mark"></span>
        <span class="brand__name">ovrik</span>
      </div>
      <p class="front__position">Company Position</p>
    </div>
  </section>

  <section class="card card--back">
    <div class="brand back__brand">
      <span class="brand__mark"></span>
      <span class="brand__name">ovrik</span>
    </div>
    <div class="back__identity">
      <p class="back__name">YourName</p>
      <p class="back__position">Company Position</p>
    </div>
    <div class="back__lines"><span></span><span></span><span></span><span></span></div>
    <p class="contact contact--phone">
      <svg class="contact__icon" viewBox="0 0 22 22" aria-hidden="true">
        <circle cx="11" cy="11" r="11" fill="#f2f2f2"/>
        <path d="M8 6.5c.6-.4 1.2-.2 1.5.4l.7 1.4c.2.5.1 1-.3 1.3l-.6.4c.5 1.2 1.4 2.1 2.6 2.6l.4-.6c.3-.4.8-.5 1.3-.3l1.4.7c.6.3.8.9.4 1.5-.6 1-1.7 1.4-2.8 1-2.7-1-4.7-3-5.7-5.7-.4-1.1 0-2.2 1.1-2.7z" fill="#050505"/>
      </svg>
      000 000 0000
    </p>
    <p class="contact contact--email">
      <svg class="contact__icon" viewBox="0 0 22 22" aria-hidden="true">
        <circle cx="11" cy="11" r="11" fill="#f2f2f2"/>
        <rect x="5.5" y="7.5" width="11" height="7.5" fill="none" stroke="#050505" stroke-width="1.2"/>
        <path d="M5.5 7.5l5.5 4.2 5.5-4.2" fill="none" stroke="#050505" stroke-width="1.2"/>
      </svg>
      name@domainname.com
    </p>
  </section>
</body>
</html>
```